Meridale Bed Company Needs Business Card

Looking for a very nice looking business card. Creative but not extravagant. We sell beds and pillows across the U.S. and need something professional but catchy. I have attached the logo.

Name : Devin Holt
Title : President
Phone : (800) 471-2960
Email: sleep@quilmora.com
Website: www.quilmora.com

Can be single-sided or double-sided
horizontal or vertical

Can use Blues/Greys

Target Market(s)

Mass Market

Industry/Entity Type

Retail

Contact Information for Business Card

Name : Devin Holt
Title : President
Phone : (800) 471-2960
Email: sleep@quilmora.com
Website: www.quilmora.com

Requirements
Must have
• Clean, Modern, Smooth
• Can use Blues/Greys
• On the other side without the information - have something simple like www.quilmora.com or our logo
Nice to have
• Surprise me
Should not have
• Nothing crazy, nothing cluttered

```html
<!DOCTYPE html>
<html lang="en">
<head>
<meta charset="UTF-8">
<title>Quilmora Business Card</title>
<link href="https://fonts.googleapis.com/css2?family=Lato:wght@300;400;700&display=swap" rel="stylesheet">
<style>
  :root {
    --backdrop: #3d3d3f;
    --card: #eef1f5;
    --brand-blue: #35a6dd;
    --ink: #3a3a3c;
    --ink-soft: #4a4a4d;
  }
  * { box-sizing: border-box; margin: 0; padding: 0; }
  html, body {
    width: 1200px;
    height: 810px;
    overflow: hidden;
    background: var(--backdrop);
    font-family: "Lato", sans-serif;
  }
  .stage {
    width: 1200px;
    height: 810px;
    display: flex;
    align-items: center;
    justify-content: center;
    gap: 44px;
  }
  .card {
    position: relative;
    width: 520px;
    height: 320px;
    background: var(--card);
    border-radius: 24px;
  }
  .wordmark {
    font-weight: 300;
    color: var(--brand-blue);
    letter-spacing: 1px;
    line-height: 1;
  }
  /* Front side */
  .card-front .wordmark {
    position: absolute;
    top: 110px;
    left: 0;
    right: 0;
    text-align: center;
    font-size: 64px;
  }
  .front-web {
    position: absolute;
    left: 0;
    right: 0;
    bottom: 56px;
    display: flex;
    align-items: center;
    justify-content: center;
    gap: 12px;
    font-size: 12px;
    color: var(--ink);
  }
  .front-web .rule {
    width: 80px;
    height: 1px;
    background: var(--brand-blue);
  }
  .front-web .accent { color: var(--brand-blue); }
  /* Back side */
  .card-back .wordmark {
    position: absolute;
    top: 48px;
    left: 40px;
    font-size: 58px;
  }
  .contact {
    position: absolute;
    left: 40px;
    bottom: 30px;
  }
  .contact-name {
    font-size: 19px;
    font-weight: 400;
    color: var(--ink);
  }
  .contact-title {
    font-size: 13px;
    color: var(--brand-blue);
    margin: 2px 0 8px 16px;
  }
  .contact-list {
    list-style: none;
    margin-left: 16px;
  }
  .contact-list li {
    display: flex;
    align-items: center;
    gap: 7px;
    font-size: 13px;
    color: var(--ink-soft);
    line-height: 19px;
  }
  .contact-list svg {
    width: 11px;
    height: 11px;
    fill: var(--brand-blue);
    flex: none;
  }
</style>
</head>
<body>
<main class="stage">
  <section class="card card-front">
    <div class="wordmark">quilmora</div>
    <div class="front-web">
      <span class="rule"></span>
      <span>www.<span class="accent">quilmora</span>.com</span>
      <span class="rule"></span>
    </div>
  </section>

  <section class="card card-back">
    <div class="wordmark">quilmora</div>
    <div class="contact">
      <div class="contact-name">Devin Holt</div>
      <div class="contact-title">President</div>
      <ul class="contact-list">
        <li>
          <svg viewBox="0 0 24 24"><path d="M6.6 10.8a15.1 15.1 0 0 0 6.6 6.6l2.2-2.2a1 1 0 0 1 1-.25 11.4 11.4 0 0 0 3.6.57 1 1 0 0 1 1 1V20a1 1 0 0 1-1 1A17 17 0 0 1 3 4a1 1 0 0 1 1-1h3.5a1 1 0 0 1 1 1c0 1.25.2 2.45.57 3.57a1 1 0 0 1-.25 1z"/></svg>
          (800) 471-2960
        </li>
        <li>
          <svg viewBox="0 0 24 24"><path d="M2 5h20v14H2z M2 5l10 8 10-8" fill="var(--brand-blue)"/><path d="M3 6l9 7 9-7" fill="none" stroke="var(--card)" stroke-width="1.8"/></svg>
          sleep@quilmora.com
        </li>
        <li>
          <svg viewBox="0 0 24 24"><circle cx="12" cy="12" r="10"/><path d="M2 12h20M12 2c3 3 3 17 0 20M12 2c-3 3-3 17 0 20" fill="none" stroke="var(--card)" stroke-width="1.5"/></svg>
          www.quilmora.com
        </li>
      </ul>
    </div>
  </section>
</main>
</body>
</html>
```